Email design required

We need a design for a paid B2B email campaign and facebook / retargeting banner ads that match the same style.

Website: http://pelmora.staging.hostvantry.com/
Campaign Name: KEX Weariness
Example: http://liftmarrowsites.com/kex-weariness/
- I made this over the weekend. It has the right words, but the style / layout needs to change

Size: 600 pixels wide, no limit on length

Formatting:
Format CSS inline only - This will ensure that size, font family, colour, line height, etc. will all remain the same once it is dropped into our newsletter sending software. See below as an

example,

Here's a mockup of

Target Market(s)

Canadian mortgage brokers

Industry/Entity Type

Campaign

Font styles to use
Sans Serif

Colors
3277b5

Requirements
Must have
• Text from my website example http://liftmarrowsites.com/kex-weariness/
• Otherwise, do whatever you think would look good.

```html
<!DOCTYPE html>
<html lang="en">
<head>
<meta charset="utf-8">
<title>Customer Review Variations</title>
<link rel="stylesheet" href="https://fonts.googleapis.com/css2?family=Open+Sans:ital,wght@0,400;0,600;0,700;1,400&display=swap">
<style>
  :root {
    --canvas-bg: #2a0b10;
    --heading-green: #74e01c;
    --brand-blue: #3184ec;
    --card-white: #ffffff;
    --quote-grey: #8a9896;
    --avatar-slate: #465257;
    --avatar-figure: #f2f2f0;
  }
  * { margin: 0; padding: 0; box-sizing: border-box; }
  html, body {
    width: 1200px;
    height: 1200px;
    overflow: hidden;
    background: var(--canvas-bg);
    font-family: "Open Sans", Arial, sans-serif;
  }
  .canvas {
    position: relative;
    width: 1200px;
    height: 1200px;
  }
  .variant-title {
    position: absolute;
    left: 0;
    width: 1142px;
    text-align: center;
    color: var(--heading-green);
    font-weight: 700;
    font-size: 33px;
    line-height: 40px;
  }
  .review-card {
    position: absolute;
    width: 721px;
  }
  .review-card__header {
    height: 58px;
    background: var(--brand-blue);
    color: #fff;
    font-weight: 700;
    font-size: 21px;
    line-height: 58px;
    text-align: center;
  }
  .review-card__body {
    position: relative;
    height: 200px;
    background: var(--card-white);
  }
  .review-card__avatar {
    position: absolute;
    left: 71px;
    top: 21px;
    width: 150px;
    height: 150px;
  }
  .review-card__photo {
    position: absolute;
    left: 76px;
    top: 8px;
    width: 138px;
    height: 174px;
    background: linear-gradient(170deg, #e0a888 0%, #c98566 50%, #1c1a1a 78%, #141212 100%);
  }
  .review-card__photo--round {
    left: 71px;
    top: 21px;
    width: 150px;
    height: 150px;
    border-radius: 50%;
    background: radial-gradient(circle at 50% 40%, #e2ac8c 0%, #c78163 42%, #3e4a50 70%, #465257 100%);
  }
  .review-card__quote {
    position: absolute;
    left: 298px;
    top: 34px;
    width: 390px;
    color: var(--quote-grey);
    font-style: italic;
    font-size: 15.5px;
    line-height: 24px;
  }
  .review-card__author {
    position: absolute;
    left: 298px;
    top: 140px;
    color: var(--quote-grey);
    font-weight: 600;
    font-size: 15.5px;
    line-height: 22px;
  }
</style>
</head>
<body>
<main class="canvas">

  <h2 class="variant-title" style="top:100px;">01 - Customer Review - No Image</h2>
  <section class="review-card" style="left:233px; top:154px;">
    <div class="review-card__header">Customer Reviews</div>
    <div class="review-card__body">
      <svg class="review-card__avatar" viewBox="0 0 150 150" aria-hidden="true">
        <circle cx="75" cy="75" r="75" fill="var(--avatar-slate)"/>
        <path d="M75 27c-13 0-21 9-21 23 0 9 3 17 8 22v8c-13 3-25 8-30 16-2 4-3 10-3 17h92c0-7-1-13-3-17-5-8-17-13-30-16v-8c5-5 8-13 8-22 0-14-8-23-21-23z" fill="var(--avatar-figure)"/>
      </svg>
      <p class="review-card__quote">I've used a few different services for this and Pelmora is by far the best. Fraction of the cost and I have the required docs within a couple of hours at most. Makes my life so much easier.</p>
      <p class="review-card__author">Dale Morrow, NWL Calgary</p>
    </div>
  </section>

  <h2 class="variant-title" style="top:461px;">02 - Customer Review - Image</h2>
  <section class="review-card" style="left:233px; top:518px;">
    <div class="review-card__header">Customer Reviews</div>
    <div class="review-card__body">
      <div class="review-card__photo" role="img" aria-label="Portrait photo of the reviewer"></div>
      <p class="review-card__quote">I've used a few different services for this and Pelmora is by far the best. Fraction of the cost and I have the required docs within a couple of hours at most. Makes my life so much easier.</p>
      <p class="review-card__author">Dale Morrow, NWL Calgary</p>
    </div>
  </section>

  <h2 class="variant-title" style="top:845px; width:1142px; left:0;">03 - Customer Review - Round Image</h2>
  <section class="review-card" style="left:227px; top:905px;">
    <div class="review-card__header">Customer Reviews</div>
    <div class="review-card__body">
      <div class="review-card__photo review-card__photo--round" role="img" aria-label="Round portrait photo of the reviewer"></div>
      <p class="review-card__quote">I've used a few different services for this and Pelmora is by far the best. Fraction of the cost and I have the required docs within a couple of hours at most. Makes my life so much easier.</p>
      <p class="review-card__author">Dale Morrow, NWL Calgary</p>
    </div>
  </section>

</main>
</body>
</html>
```